Keystone Polished Concrete & Grinding
I'm looking for a business card and logo design for my
new Polished Concrete & Grinding business,
If you were to look up Keystone in the dictionary it would
say, first in importance, order, or position; leading.
Polished Concrete floors are a niche market, that are being used currently in Shopping centres, office spaces and by most high end architects, builders and designers.
i need my business card & logo to stand out from my
competitors, i need my design + logo to reflect this it
needs to be simple, professional, eye catching, easy
to read and scream quality. The logo will need to be
suitable for a whole range of applications including,
uniforms, letter heads, stickers, and eventually
incorporating in vehicle vinyl wrapping.
Target Market(s)
Builders, architects, Interior designers & home owners
Contact Information for Business Card
Front side:
- Keystone Polished Concrete & Grinding.
- Logo
Rear side:
- Liam Varesko
- 0438175092
- info@keystonepcg-example.com.au
- commercial - domestic - industrial
- (later down the line website & space for
social media links
www.keystonepolishedslab-example.com.au)
Colors
Designer to choose colors to be used in the design.
Look and feel
Each slider illustrates characteristics of the customer's brand and the style your logo design should communicate.

```html
<!DOCTYPE html>
<html lang="en">
<head>
<meta charset="utf-8">
<title>Keystone Polished Concrete &amp; Grinding — Business Card</title>
<link rel="stylesheet" href="https://fonts.googleapis.com/css2?family=Roboto:wght@400;500&display=swap">
<style>
  :root {
    --backdrop: #232323;
    --card: #1c1c1c;
    --card-edge: #2a2a2a;
    --ink-light: #f2f2f2;
    --ink-silver: #c8c8c8;
    --accent-blue: #29a8df;
  }
  * { margin: 0; padding: 0; box-sizing: border-box; }
  html, body {
    width: 1200px;
    height: 900px;
    overflow: hidden;
    background: var(--backdrop);
    font-family: "Roboto", sans-serif;
  }
  .canvas {
    position: relative;
    width: 1200px;
    height: 900px;
  }
  .card {
    position: absolute;
    left: 280px;
    width: 640px;
    height: 366px;
    background: var(--card);
    border: 1px solid var(--card-edge);
    box-shadow: 0 10px 30px rgba(0,0,0,0.55);
    overflow: hidden;
  }
  .card--front { top: 60px; }
  .card--back { top: 470px; }

  /* Front */
  .front-name {
    position: absolute;
    left: 0; right: 0;
    top: 110px;
    text-align: center;
    color: var(--ink-silver);
    font-weight: 500;
    font-size: 30px;
    line-height: 1.25;
    letter-spacing: 1px;
    text-transform: uppercase;
  }
  .front-services {
    position: absolute;
    left: 0; right: 0;
    bottom: 46px;
    text-align: center;
    color: var(--ink-light);
    font-size: 15px;
    letter-spacing: 1px;
  }

  /* Back */
  .back-name {
    position: absolute;
    left: 24px;
    top: 132px;
    width: 244px;
    text-align: center;
    color: var(--accent-blue);
    font-weight: 500;
    font-size: 19px;
    line-height: 1.3;
    letter-spacing: 0.5px;
    text-transform: uppercase;
    white-space: nowrap;
  }
  .divider {
    position: absolute;
    left: 290px;
    top: 80px;
    width: 2px;
    height: 200px;
    background: var(--accent-blue);
  }
  .person {
    position: absolute;
    left: 312px;
    right: 14px;
    top: 98px;
  }
  .person__name {
    color: var(--accent-blue);
    font-weight: 500;
    font-size: 30px;
    letter-spacing: 3px;
    text-transform: uppercase;
    white-space: nowrap;
  }
  .person__role {
    color: var(--ink-light);
    font-size: 16px;
    margin-top: 2px;
  }
  .contact {
    list-style: none;
    margin-top: 24px;
  }
  .contact__item {
    display: flex;
    align-items: center;
    gap: 9px;
    color: var(--ink-light);
    font-size: 14px;
    line-height: 27px;
    white-space: nowrap;
  }
  .contact__icon {
    width: 12px;
    height: 12px;
    flex: none;
  }
</style>
</head>
<body>
<main class="canvas">

  <section class="card card--front" aria-label="Business card front">
    <p class="front-name">Keystone Polished<br>Concrete &amp; Grinding</p>
    <p class="front-services">COMMERCIAL - DOMESTIC - INDUSTRIAL</p>
  </section>

  <section class="card card--back" aria-label="Business card back">
    <p class="back-name">Keystone Polished<br>Concrete &amp; Grinding</p>
    <div class="divider"></div>
    <div class="person">
      <h1 class="person__name">Liam Varesko</h1>
      <p class="person__role">Director</p>
      <ul class="contact">
        <li class="contact__item">
          <svg class="contact__icon" viewBox="0 0 12 12" aria-hidden="true">
            <path d="M2.5 1 L4.5 1 L5.2 3.6 L4 4.6 Q5 7 7.4 8 L8.4 6.8 L11 7.5 L11 9.5 Q10 11 8.5 11 Q2 10 1 3.5 Q1 2 2.5 1 Z" fill="var(--accent-blue)"/>
          </svg>
          0438175092
        </li>
        <li class="contact__item">
          <svg class="contact__icon" viewBox="0 0 12 12" aria-hidden="true">
            <rect x="0.75" y="2.25" width="10.5" height="7.5" fill="none" stroke="var(--accent-blue)" stroke-width="1.2"/>
            <path d="M1 2.7 L6 6.5 L11 2.7" fill="none" stroke="var(--accent-blue)" stroke-width="1.2"/>
          </svg>
          info@keystonepcg-example.com.au
        </li>
        <li class="contact__item">
          <svg class="contact__icon" viewBox="0 0 12 12" aria-hidden="true">
            <circle cx="6" cy="6" r="5.2" fill="none" stroke="var(--accent-blue)" stroke-width="1"/>
            <ellipse cx="6" cy="6" rx="2.3" ry="5.2" fill="none" stroke="var(--accent-blue)" stroke-width="1"/>
            <path d="M0.8 6 H11.2 M1.8 3.3 H10.2 M1.8 8.7 H10.2" stroke="var(--accent-blue)" stroke-width="0.9"/>
          </svg>
          www.keystonepolishedslab-example.com.au
        </li>
      </ul>
    </div>
  </section>

</main>
</body>
</html>
```